Fizz's Shed & Grill Burger Restaurant Website - HomePage Only PSD

I need a website design for a restaurant called "Fizz's Shed and Grill" featuring burgers, wings, beer, live music, trivia, and more. I have several images of the restaurant and they already have their logo files created (see attached). I want some type of wood background and integrate the silver tin. This needs to be a modern, hip and fun type design. Design must incorporate these attached graphics.

UPDATE - just added a few more images of things I really like to be incorporated into my designs.
Updates

Industry/Entity Type

Burger Restaurant

Number of Pages Required

1 page

Font styles to use
Sans Serif

Requirements
Must have
• Restaurant/Bar theme with integration of existing logo and the red wood look.
Nice to have
• - Modern Fun appearance
• - Use Pelko Fonts

```html
<!DOCTYPE html>
<html lang="en">
<head>
<meta charset="utf-8">
<title>Fizz's Shed and Grill</title>
<link href="https://fonts.googleapis.com/css2?family=Mystery+Quest&family=Raleway:wght@400;500;600&display=swap" rel="stylesheet">
<style>
:root{
  --wood-light:#b07a48;
  --wood-mid:#8f5c33;
  --wood-dark:#6a3f20;
  --plank-line:rgba(60,32,14,.35);
  --grass:#7cae2c;
  --grass-dark:#3f7a1c;
  --hay:#d8d36a;
  --panel:#1d1916;
  --gold:#e0962a;
  --cream:#fff6e4;
  --ink:#2b2118;
  --white:#ffffff;
  --footer:#3a200f;
  --silver-hi:#f2f2f2;
  --silver-lo:#8a8a8a;
  --display:'Mystery Quest', cursive;
  --body:'Raleway', sans-serif;
}
*{margin:0;padding:0;box-sizing:border-box}
html,body{width:1200px;height:2400px;overflow:hidden}
body{position:relative;font-family:var(--body);color:var(--ink);
  background:
    repeating-linear-gradient(90deg,transparent 0 62px,var(--plank-line) 62px 65px),
    linear-gradient(180deg,var(--wood-light),var(--wood-mid) 60%,var(--wood-dark));}
.abs{position:absolute}

/* hero */
.hero-art{left:0;top:0;width:1200px;height:560px;
  background:linear-gradient(180deg,var(--hay) 0%,#b9c95a 30%,var(--grass) 60%,var(--grass-dark) 100%);
  border-radius:0 0 50% 50% / 0 0 70px 70px}
.nav-rule{left:99px;width:1002px;height:2px;background:rgba(60,60,20,.55)}
.nav a{position:absolute;top:98px;font-size:16px;color:#2a2a10;text-decoration:none;font-weight:500}
.brand{left:525px;top:32px;width:150px;height:150px;border-radius:50%;
  background:radial-gradient(circle at 40% 35%,#7ec235,#3f8a18);border:4px solid #e9f2c9;
  display:flex;align-items:center;justify-content:center;text-align:center;
  font-family:var(--display);color:var(--white);font-size:21px;line-height:1.1;padding:16px}
.hero-title{left:106px;top:425px;font-family:var(--display);font-size:40px;color:var(--white);font-weight:400}
.pager{top:573px;width:42px;height:42px;border-radius:50%;background:var(--white);
  border:3px solid #2f5e14;display:flex;align-items:center;justify-content:center;
  font-family:var(--display);font-size:20px;color:#1a1a1a}

/* about */
.about{left:128px;top:678px;width:944px;height:282px;border-radius:14px;
  background:var(--wood-dark);padding:14px}
.about-inner{width:100%;height:100%;background:var(--cream);border-radius:8px;position:relative;
  box-shadow:inset 0 0 0 3px #d9c6a4}
.mini-mark{width:46px;height:46px;border-radius:50%;border:2px solid var(--ink);background:var(--white)}
.about-title{left:123px;top:48px;font-family:var(--display);font-size:35px;color:var(--ink);font-weight:400}
.about-text{left:44px;top:114px;width:640px;font-size:13.5px;line-height:22px}
.about-photo{left:714px;top:41px;width:164px;height:168px;border-radius:10px;border:5px solid var(--wood-dark);
  background:linear-gradient(180deg,#a9c3d6,#b49a86)}

/* specialities */
.specials{left:101px;top:1035px;width:998px;height:866px;background:var(--panel);border:5px solid var(--gold)}
.specials-title{left:0;top:36px;width:100%;display:flex;justify-content:center;align-items:center;gap:16px;
  font-family:var(--display);font-size:36px;color:var(--cream);font-weight:400}
.flourish{left:441px;top:104px;width:106px;height:14px;border-radius:7px;
  background:linear-gradient(90deg,transparent,var(--gold),transparent)}
.dish{top:268px;width:262px;height:262px;border-radius:50%;border:2px solid var(--gold);text-align:center;color:var(--cream)}
.disc{left:78px;top:-55px;width:106px;height:106px;border-radius:50%;
  background:radial-gradient(circle at 35% 30%,var(--silver-hi),#bdbdbd 45%,var(--silver-lo));
  display:flex;align-items:center;justify-content:center;box-shadow:0 3px 8px rgba(0,0,0,.5)}
.dish h3{margin-top:75px;font-family:var(--display);font-weight:400;font-size:33px}
.dish p{margin:14px auto 0;width:190px;font-size:13px;line-height:24px}
.read-more{display:inline-block;margin-top:14px;width:80px;height:20px;background:#e6d2ad;
  font-family:var(--display);font-size:10px;line-height:20px;color:var(--ink)}
.banner{left:11px;top:555px;width:966px;height:237px;
  background:linear-gradient(100deg,#e09a3c,#f0b95c 45%,#d9872b)}
.banner h2{position:absolute;left:32px;top:36px;font-family:var(--display);font-weight:400;font-size:28px;line-height:38px;color:var(--cream)}
.banner p{position:absolute;left:32px;top:132px;width:560px;font-size:13px;line-height:24px;color:var(--white)}
.burger-art{left:664px;top:30px;width:290px;height:180px;border-radius:16px;
  background:linear-gradient(160deg,#c77a30,#9a5424)}

/* foot */
.meadow{left:0;top:1952px;width:1200px;height:328px;
  background:linear-gradient(180deg,transparent 0%,rgba(124,174,44,.25) 55%,var(--grass) 85%,var(--grass-dark) 100%)}
.sign{left:909px;top:2168px;width:224px;height:64px;background:#d9c29a;border:3px solid #8a6a44;
  display:flex;align-items:center;justify-content:center;gap:8px;font-family:var(--display);font-size:16px;color:var(--ink)}
.sign .dot{width:30px;height:30px;border-radius:50%;border:2px solid var(--ink)}
.footer{left:0;top:2280px;width:1200px;height:120px;background:var(--footer)}
.copyright{left:99px;top:68px;font-family:var(--display);font-size:16px;color:var(--cream)}
.thumb{top:60px;width:40px;height:40px;border:2px solid var(--cream)}
.social{top:62px;width:36px;height:36px;border-radius:50%;border:2px solid var(--cream)}
</style>
</head>
<body>
<div class="abs hero-art" role="img" aria-label="Illustrated farmland with rolling green fields, red barn, silos, trees and a cow peeking in"></div>
<div class="abs nav-rule" style="top:75px"></div>
<div class="abs nav-rule" style="top:136px"></div>
<nav class="nav">
  <a style="left:147px">Home</a>
  <a style="left:229px">About Us</a>
  <a style="left:341px">Our Specialities</a>
  <a style="left:738px">Live Music</a>
  <a style="left:864px">Trivia</a>
  <a style="left:952px">Contact Us</a>
</nav>
<div class="abs brand">Fizz's Shed and Grill</div>
<h1 class="abs hero-title">Fizz's Shed and Grill</h1>
<div class="abs pager" style="left:494px">1</div>
<div class="abs pager" style="left:577px">2</div>
<div class="abs pager" style="left:661px">3</div>

<section class="abs about">
  <div class="about-inner">
    <div class="abs mini-mark" style="left:62px;top:48px"></div>
    <h2 class="abs about-title">Fizz's Shed and Grill</h2>
    <p class="abs about-text">Our restaurant is about burgers, wings, beer, live music, trivia, etc. Nemo enim ipsam voluptatem quia voluptas sit aspernatur aut odit aut fugit, sed quia consequuntur magni dolores eos qui ratione voluptatem sequi nesciunt. Neque porro quisquam est, quidolo rem ipsum quia dolor sit amet, consectetur, adipisci velit</p>
    <div class="abs about-photo" role="img" aria-label="Photo of the restaurant building front"></div>
  </div>
</section>

<section class="abs specials">
  <h2 class="abs specials-title"><span class="mini-mark" style="width:40px;height:40px;display:inline-block"></span>Our Specialities</h2>
  <div class="abs flourish" role="img" aria-label="Decorative flourish"></div>

  <div class="abs dish" style="left:48px">
    <div class="abs disc"><svg width="44" height="40" viewBox="0 0 44 40" fill="#1a1a1a"><path d="M4 16a18 14 0 0 1 36 0z"/><rect x="2" y="19" width="40" height="5" rx="2"/><rect x="4" y="27" width="36" height="8" rx="4"/></svg></div>
    <h3>Burgers</h3>
    <p>Nemo enim ipsam voluptatem quia voluptas sit aspernatur aut dodit aut fugit</p>
    <span class="read-more">Read More</span>
  </div>
  <div class="abs dish" style="left:368px">
    <div class="abs disc"><svg width="44" height="40" viewBox="0 0 44 40"><path d="M6 20c0-10 10-15 20-13s14 10 12 17-10 10-20 8S6 28 6 20z" fill="#1a1a1a"/><circle cx="18" cy="19" r="4" fill="#ddd"/></svg></div>
    <h3>Wings</h3>
    <p>Nemo enim ipsam voluptatem quia voluptas sit aspernatur aut dodit aut fugit</p>
    <span class="read-more">Read More</span>
  </div>
  <div class="abs dish" style="left:688px">
    <div class="abs disc"><svg width="40" height="44" viewBox="0 0 40 44" fill="none" stroke="#1a1a1a" stroke-width="4"><rect x="6" y="6" width="20" height="34" rx="2"/><path d="M26 14h6a4 4 0 0 1 4 4v8a4 4 0 0 1-4 4h-6"/></svg></div>
    <h3>Beer</h3>
    <p>Nemo enim ipsam voluptatem quia voluptas sit aspernatur aut dodit aut fugit</p>
    <span class="read-more">Read More</span>
  </div>

  <div class="abs banner">
    <h2>Our restaurant is about burgers,<br>wings, beer, live music</h2>
    <p>Nemo enim ipsam voluptatem quia voluptas sit aspernatur aut odit aut fugit, sed quia consequuntur magni dolores eos qui ratione voluptatem sequi nesciunt. Neque porro quisquam est, qui dolorem ipsum</p>
    <div class="abs burger-art" role="img" aria-label="Photo of a cheeseburger"></div>
  </div>
</section>

<div class="abs meadow" role="img" aria-label="Illustrated meadow with trees, grass and a grazing cow"></div>
<div class="abs sign"><span class="dot"></span>Fizz's Shed and Grill</div>

<footer class="abs footer">
  <p class="abs copyright">© Fizz's Shed and Grill 2016 - All rights reserved.</p>
  <div class="abs thumb" style="left:779px;background:linear-gradient(135deg,#c98a3a,#6a3f20)" role="img" aria-label="Small food photo"></div>
  <div class="abs thumb" style="left:840px;background:linear-gradient(135deg,#8aa0c0,#4a5a70)" role="img" aria-label="Small venue photo"></div>
  <span class="abs social" style="left:899px"></span>
  <span class="abs social" style="left:955px"></span>
  <span class="abs social" style="left:1011px"></span>
  <span class="abs social" style="left:1067px"></span>
</footer>
</body>
</html>
```